Summit Bodyform Gym Website

We need a website design for our gym.

Summit is the UAE's first calisthenics and parkour gym. The theme under which the gym revolves is that one does not require any machinery to workout as our bodies could be themselves the machinery. The gym is designed to be the more of a social hub rather than an "in-and-out" gym, where people come train, have fun, hang out and socialize for a few hours rather than just train for 60 minutes then leave. The gym is designed to be a big open space with lots of natural sunlight, natural wood and plants all over the place to create a natural and refreshing setting. We also use recycled material throughout the gym and recycle our waste as being green is part of our philosophy. We currently also have some of the world's top and most recognized calisthenics athletes working with us.

We would like our website to reflect all that as well as provide a simple, interactive and fun way for visitors to be able to get class and gym information, check out gym media and contact us for bookings.

Target Market(s)

Ages 15-35

Industry/Entity Type

Fitness

Coding

Coded - Design and coding required

Number of Pages Required

4 page

Font styles to use
Decorative

Colors
0792cd

Requirements
Must have
• Class descriptions
• Gym description
• Class schedules
• Trainer profiles
• Gym philosophy
• Contact Details
Nice to have
• A link to contact us directly for a free first trial class

```html
<!DOCTYPE html>
<html lang="en">
<head>
<meta charset="utf-8">
<title>Summit Bodyform Gym</title>
<link href="https://fonts.googleapis.com/css2?family=Oswald:wght@400;500;700&family=Roboto+Condensed:ital,wght@0,400;0,700;1,400&display=swap" rel="stylesheet">
<style>
:root{
  --brand:#0792cd;
  --band:#0a99c8;
  --band-dark:#0a86b8;
  --nav-top:#28c6f0;
  --nav-bottom:#079fd5;
  --nav-active:#0b8fc3;
  --ink:#1b1b1b;
  --body:#444;
  --white:#fff;
  --footer-name:#0a7bab;
}
*{margin:0;padding:0;box-sizing:border-box}
html,body{width:1200px;height:2594px;overflow:hidden;background:var(--white)}
body{position:relative;font-family:"Roboto Condensed",Arial,sans-serif;color:var(--body)}
.abs{position:absolute}
h1,h2,h3,.nav a,.btn{font-family:"Oswald",Arial,sans-serif;font-weight:400}

/* header */
.site-header{position:absolute;left:0;top:0;width:1200px;height:152px;border-top:5px solid var(--brand)}
.brand-name{position:absolute;left:100px;top:48px;font-family:"Oswald",sans-serif;font-weight:400;font-size:34px;line-height:1;color:var(--ink);white-space:nowrap}
.contact-chip{position:absolute;top:52px;display:flex;align-items:center;gap:12px;font-size:14px;color:#333;white-space:nowrap}
.chip-icon{width:42px;height:42px;border-radius:50%;background:var(--brand);display:flex;align-items:center;justify-content:center}
.search{position:absolute;left:871px;top:52px;width:230px;height:43px;display:flex;box-shadow:0 1px 3px rgba(0,0,0,.15)}
.search span{flex:1;font-size:12px;color:#888;padding:13px 14px;background:#fafafa;border:1px solid #e4e4e4}
.search i{width:46px;background:var(--brand);display:flex;align-items:center;justify-content:center}

/* nav */
.nav{position:absolute;left:0;top:152px;width:1200px;height:45px;background:linear-gradient(var(--nav-top),var(--nav-bottom));display:flex;padding-left:99px}
.nav a{color:var(--white);text-decoration:none;font-size:14px;line-height:45px;padding:0 20px}
.nav a.active{background:var(--nav-active);padding:0 27px}

/* hero */
.hero{position:absolute;left:0;top:197px;width:1200px;height:412px;background:linear-gradient(90deg,#1c1c1c 0%,#2e2e2e 35%,#3b4a52 60%,#5d6b60 80%,#394a5a 100%)}
.hero h1{position:absolute;left:98px;top:88px;font-size:38px;line-height:48px;color:var(--white)}
.btn{display:inline-block;background:linear-gradient(#22c2ef,#0aa5da);color:var(--white);text-decoration:none}
.hero .btn{position:absolute;left:98px;top:204px;width:191px;height:57px;line-height:57px;text-align:center;font-size:18px}
.dots{position:absolute;left:96px;top:294px;display:flex;gap:9px}
.dots b{width:8px;height:8px;border-radius:50%;background:#ddd}
.dots b:first-child{background:#1fb8ea}

/* bands */
.band{position:absolute;left:0;width:1200px;background:var(--band);color:var(--white)}
.band h2{font-size:36px;color:var(--white)}
.band p{font-size:13px;line-height:20.5px;margin-bottom:20px}
.photo{position:absolute}
.more{color:var(--white);font-size:13px;text-decoration:none}

.section-title{position:absolute;left:0;width:1200px;text-align:center;font-family:"Oswald",sans-serif;font-weight:400;font-size:36px;color:var(--ink)}

/* trainers */
.trainer{position:absolute;width:330px;text-align:center}
.trainer .avatar{width:194px;height:194px;border-radius:50%;margin:0 auto;background:radial-gradient(circle at 50% 45%,#b58c6e,#4a3a34 70%)}
.trainer h3{font-size:36px;color:var(--brand);margin-top:21px;line-height:50px}
.trainer p{font-size:13px;line-height:20.5px;color:#444;margin:6px 14px 0}
.trainer a{display:block;margin-top:16px;font-size:13px;color:var(--brand);text-decoration:none}

/* class list */
.class-list{position:absolute;list-style:none;font-size:14px}
.class-list li{height:30.8px;display:flex;align-items:center;gap:12px;white-space:nowrap}
.arrow{width:14px;height:14px;flex:none}

/* testimonials */
.quote{position:absolute;width:520px;height:140px}
.quote .avatar{position:absolute;left:0;top:0;width:114px;height:114px;border-radius:50%;background:radial-gradient(circle at 50% 40%,#a67b62,#3b3332 70%)}
.quote .mark{position:absolute;left:126px;top:-10px;font-family:Georgia,serif;font-size:70px;color:#bdbdbd;line-height:1}
.quote p{position:absolute;left:172px;top:-2px;width:320px;text-align:center;font-size:13px;line-height:20.5px;color:#444}
.quote cite{position:absolute;left:172px;top:72px;width:320px;text-align:center;font-size:13px;color:var(--brand)}

/* footer */
.footer{position:absolute;left:0;top:2244px;width:1200px;height:280px;background:var(--band);color:var(--white)}
.footer h2{position:absolute;top:38px;font-size:26px;color:var(--white)}
.footer ul{position:absolute;left:98px;top:88px;list-style:none;font-size:11px;line-height:20.7px}
.footer .small{font-size:11px;line-height:20px}
.field{position:absolute;left:311px;top:142px;width:218px;height:43px;background:var(--white);color:#777;font-size:11px;display:flex;align-items:center;gap:10px;padding-left:14px;border-radius:2px}
.subscribe{position:absolute;left:315px;top:201px;width:77px;height:34px;background:#111;color:var(--white);font-size:10px;text-align:center;line-height:34px;border-radius:3px}
.info{position:absolute;left:593px;display:flex;gap:10px;font-size:11px;line-height:20px}
.footer-name{position:absolute;left:860px;top:80px;font-family:"Oswald",sans-serif;font-weight:400;font-size:32px;line-height:1;color:var(--footer-name);white-space:nowrap}
.bottom-bar{position:absolute;left:0;top:2524px;width:1200px;height:70px;background:var(--band-dark);color:var(--white)}
.bottom-bar small{position:absolute;left:98px;top:28px;font-size:10px}
.social{position:absolute;left:973px;top:19px;display:flex;gap:1px}
.social b{width:32px;height:32px;border-radius:50%;background:var(--white)}
</style>
</head>
<body>

<header class="site-header">
  <div class="brand-name">Summit Bodyform Gym</div>
  <div class="contact-chip" style="left:477px">
    <span class="chip-icon"><svg width="20" height="20" viewBox="0 0 24 24"><path fill="#fff" d="M6.6 10.8a15 15 0 0 0 6.6 6.6l2.2-2.2c.3-.3.7-.4 1-.2 1.1.4 2.3.6 3.6.6.6 0 1 .4 1 1V20c0 .6-.4 1-1 1A17 17 0 0 1 3 4c0-.6.4-1 1-1h3.5c.6 0 1 .4 1 1 0 1.3.2 2.5.6 3.6.1.3 0 .7-.2 1z"/></svg></span>
    1800-555-012
  </div>
  <div class="contact-chip" style="left:660px">
    <span class="chip-icon"><svg width="20" height="16" viewBox="0 0 20 16"><rect x="1" y="1" width="18" height="14" rx="2" fill="#fff"/><path d="M2 3l8 6 8-6" stroke="#0792cd" stroke-width="2" fill="none"/></svg></span>
    info@summitgym.ae
  </div>
  <div class="search"><span>Search</span><i><svg width="18" height="18" viewBox="0 0 20 20"><circle cx="8" cy="8" r="6" stroke="#fff" stroke-width="2.5" fill="none"/><path d="M12.5 12.5L18 18" stroke="#fff" stroke-width="2.5"/></svg></i></div>
</header>

<nav class="nav">
  <a class="active" href="#">Home</a>
  <a href="#">Class descriptions</a>
  <a href="#">Gym description</a>
  <a href="#">Class schedules</a>
  <a href="#">Trainer profiles</a>
  <a href="#">Gym philosophy</a>
  <a href="#">Contact</a>
</nav>

<section class="hero" role="img" aria-label="Athlete training on a pull-up bar inside the gym">
  <h1>FREE FIRST TRIAL<br>CLASS</h1>
  <a class="btn" href="#">GET STARTED NOW</a>
  <div class="dots"><b></b><b></b><b></b></div>
</section>

<section class="band" style="top:609px;height:425px">
  <div class="abs" style="left:35px;top:46px;width:530px">
    <h2>GYM DESCRIPTION</h2>
    <div style="margin-top:12px">
      <p>Nemo enim ipsam voluptatem quia voluptas sit aspernatur aut odit aut fugit, sed quia consequuntur magni dolores eos qui ratione voluptatem sequi nesciunt. Neque porro quisquam est, qui dolorem ipsum quia dolor sit amet, consectetur, adipisci velit, sed quia non numquam eius modi tempora incidunt ut labore et dolore magnam aliquam quaerat voluptatem.</p>
      <p>Ut enim ad minima veniam, quis nostrum exercitationem ullam corporis suscipit laboriosam, nisi ut aliquid ex ea commodi consequatur? Quis autem vel eum iure reprehenderit qui in ea voluptate velit esse quam nihil molestiae consequatur</p>
      <p>At vero eos et accusamus et iusto odio dignissimos ducimus qui blanditiis praesentium voluptatum deleniti atque corrupti quos dolores et quas molestias excepturi sint occaecati cupiditate non provident, similique sunt in culpa qui officia deserunt mollitia animi</p>
      <a class="more" href="#">Read More</a>
    </div>
  </div>
  <div class="photo" role="img" aria-label="Gym interior with a green plant wall, dumbbell rack and squat racks" style="left:597px;top:0;width:603px;height:425px;background:linear-gradient(180deg,#8a6a4c 0%,#6f5a44 35%,#3d3a38 60%,#9b4a3c 100%)"></div>
</section>

<h2 class="section-title" style="top:1062px">OUR TRAINER</h2>
<div class="trainer" style="left:86px;top:1132px"><div class="avatar" role="img" aria-label="Portrait of trainer Lena Maris"></div><h3>LENA MARIS</h3><p>Nemo enim ipsam voluptatem quia voluptas sit aspernatur aut odit aut fugit, sed quia consequuntur magni dolores eos qui ratione voluptatem</p><a href="#">Read More</a></div>
<div class="trainer" style="left:435px;top:1132px"><div class="avatar" role="img" aria-label="Portrait of trainer Joel"></div><h3>JOEL</h3><p>Nemo enim ipsam voluptatem quia voluptas sit aspernatur aut odit aut fugit, sed quia consequuntur magni dolores eos qui ratione voluptatem</p><a href="#">Read More</a></div>
<div class="trainer" style="left:781px;top:1132px"><div class="avatar" role="img" aria-label="Portrait of trainer Ironpeak on gymnastic rings"></div><h3>IRONPEAK</h3><p>Nemo enim ipsam voluptatem quia voluptas sit aspernatur aut odit aut fugit, sed quia consequuntur magni dolores eos qui ratione voluptatem</p><a href="#">Read More</a></div>

<section class="band" style="top:1539px;height:425px">
  <div class="photo" role="img" aria-label="Bright open training hall with blue floor mats" style="left:0;top:0;width:600px;height:425px;background:linear-gradient(180deg,#dfe6ea 0%,#b9c3c8 40%,#8a4a3e 62%,#7d3f36 100%)"></div>
  <div class="abs" style="left:631px;top:44px;width:550px">
    <h2>CLASS DESCRIPTIONS</h2>
    <p style="margin-top:10px">Nemo enim ipsam voluptatem quia voluptas sit aspernatur aut odit aut fugit, sed quia consequuntur magni dolores eos qui ratione voluptatem</p>
  </div>
  <ul class="class-list" style="left:635px;top:166px">
    <li><svg class="arrow" viewBox="0 0 14 14"><circle cx="7" cy="7" r="7" fill="#fff"/><path d="M4 7h5M7 4.5L9.5 7 7 9.5" stroke="#0a99c8" stroke-width="1.8" fill="none"/></svg>Double Salmon Ladder</li>
    <li><svg class="arrow" viewBox="0 0 14 14"><circle cx="7" cy="7" r="7" fill="#fff"/><path d="M4 7h5M7 4.5L9.5 7 7 9.5" stroke="#0a99c8" stroke-width="1.8" fill="none"/></svg>Unstable Bridge</li>
    <li><svg class="arrow" viewBox="0 0 14 14"><circle cx="7" cy="7" r="7" fill="#fff"/><path d="M4 7h5M7 4.5L9.5 7 7 9.5" stroke="#0a99c8" stroke-width="1.8" fill="none"/></svg>Cliff Hanger</li>
    <li><svg class="arrow" viewBox="0 0 14 14"><circle cx="7" cy="7" r="7" fill="#fff"/><path d="M4 7h5M7 4.5L9.5 7 7 9.5" stroke="#0a99c8" stroke-width="1.8" fill="none"/></svg>Vertical Climbing Bars</li>
    <li><svg class="arrow" viewBox="0 0 14 14"><circle cx="7" cy="7" r="7" fill="#fff"/><path d="M4 7h5M7 4.5L9.5 7 7 9.5" stroke="#0a99c8" stroke-width="1.8" fill="none"/></svg>Hanging Globes</li>
    <li><svg class="arrow" viewBox="0 0 14 14"><circle cx="7" cy="7" r="7" fill="#fff"/><path d="M4 7h5M7 4.5L9.5 7 7 9.5" stroke="#0a99c8" stroke-width="1.8" fill="none"/></svg>Climbing Ropes</li>
    <li><svg class="arrow" viewBox="0 0 14 14"><circle cx="7" cy="7" r="7" fill="#fff"/><path d="M4 7h5M7 4.5L9.5 7 7 9.5" stroke="#0a99c8" stroke-width="1.8" fill="none"/></svg>Rope Jungle</li>
  </ul>
  <ul class="class-list" style="left:832px;top:166px">
    <li><svg class="arrow" viewBox="0 0 14 14"><circle cx="7" cy="7" r="7" fill="#fff"/><path d="M4 7h5M7 4.5L9.5 7 7 9.5" stroke="#0a99c8" stroke-width="1.8" fill="none"/></svg>Quad Steps</li>
    <li><svg class="arrow" viewBox="0 0 14 14"><circle cx="7" cy="7" r="7" fill="#fff"/><path d="M4 7h5M7 4.5L9.5 7 7 9.5" stroke="#0a99c8" stroke-width="1.8" fill="none"/></svg>Rolling Log</li>
    <li><svg class="arrow" viewBox="0 0 14 14"><circle cx="7" cy="7" r="7" fill="#fff"/><path d="M4 7h5M7 4.5L9.5 7 7 9.5" stroke="#0a99c8" stroke-width="1.8" fill="none"/></svg>Floating Doors</li>
    <li><svg class="arrow" viewBox="0 0 14 14"><circle cx="7" cy="7" r="7" fill="#fff"/><path d="M4 7h5M7 4.5L9.5 7 7 9.5" stroke="#0a99c8" stroke-width="1.8" fill="none"/></svg>Floating Stairs</li>
    <li><svg class="arrow" viewBox="0 0 14 14"><circle cx="7" cy="7" r="7" fill="#fff"/><path d="M4 7h5M7 4.5L9.5 7 7 9.5" stroke="#0a99c8" stroke-width="1.8" fill="none"/></svg>Ring Climb</li>
    <li><svg class="arrow" viewBox="0 0 14 14"><circle cx="7" cy="7" r="7" fill="#fff"/><path d="M4 7h5M7 4.5L9.5 7 7 9.5" stroke="#0a99c8" stroke-width="1.8" fill="none"/></svg>Trampolines</li>
    <li><svg class="arrow" viewBox="0 0 14 14"><circle cx="7" cy="7" r="7" fill="#fff"/><path d="M4 7h5M7 4.5L9.5 7 7 9.5" stroke="#0a99c8" stroke-width="1.8" fill="none"/></svg>Foam Pit</li>
  </ul>
  <ul class="class-list" style="left:986px;top:166px">
    <li><svg class="arrow" viewBox="0 0 14 14"><circle cx="7" cy="7" r="7" fill="#fff"/><path d="M4 7h5M7 4.5L9.5 7 7 9.5" stroke="#0a99c8" stroke-width="1.8" fill="none"/></svg>Rock Wall</li>
    <li><svg class="arrow" viewBox="0 0 14 14"><circle cx="7" cy="7" r="7" fill="#fff"/><path d="M4 7h5M7 4.5L9.5 7 7 9.5" stroke="#0a99c8" stroke-width="1.8" fill="none"/></svg>Zip Line</li>
    <li><svg class="arrow" viewBox="0 0 14 14"><circle cx="7" cy="7" r="7" fill="#fff"/><path d="M4 7h5M7 4.5L9.5 7 7 9.5" stroke="#0a99c8" stroke-width="1.8" fill="none"/></svg>Jumping Pillow</li>
    <li><svg class="arrow" viewBox="0 0 14 14"><circle cx="7" cy="7" r="7" fill="#fff"/><path d="M4 7h5M7 4.5L9.5 7 7 9.5" stroke="#0a99c8" stroke-width="1.8" fill="none"/></svg>Calisthenic Rack</li>
    <li><svg class="arrow" viewBox="0 0 14 14"><circle cx="7" cy="7" r="7" fill="#fff"/><path d="M4 7h5M7 4.5L9.5 7 7 9.5" stroke="#0a99c8" stroke-width="1.8" fill="none"/></svg>Weight Training Equipment</li>
    <li><svg class="arrow" viewBox="0 0 14 14"><circle cx="7" cy="7" r="7" fill="#fff"/><path d="M4 7h5M7 4.5L9.5 7 7 9.5" stroke="#0a99c8" stroke-width="1.8" fill="none"/></svg>Slacklines</li>
    <li><svg class="arrow" viewBox="0 0 14 14"><circle cx="7" cy="7" r="7" fill="#fff"/><path d="M4 7h5M7 4.5L9.5 7 7 9.5" stroke="#0a99c8" stroke-width="1.8" fill="none"/></svg>Warped Wall</li>
  </ul>
</section>

<h2 class="section-title" style="top:2005px">TESTIMONIAL</h2>
<div class="quote" style="left:99px;top:2083px">
  <div class="avatar" role="img" aria-label="Photo of gym member Samira"></div>
  <span class="mark">&ldquo;</span>
  <p>Nemo enim ipsam voluptatem quia voluptas sit aspernatur aut odit aut fugit, sed quia consequuntur magni dolores eos qui ratione voluptatem</p>
  <cite>Samira</cite>
</div>
<div class="quote" style="left:631px;top:2083px">
  <div class="avatar" role="img" aria-label="Photo of gym member clarisse"></div>
  <span class="mark">&ldquo;</span>
  <p>Nemo enim ipsam voluptatem quia voluptas sit aspernatur aut odit aut fugit, sed quia consequuntur magni dolores eos qui ratione voluptatem</p>
  <cite>clarisse</cite>
</div>

<footer class="footer">
  <div class="footer-name">Summit Bodyform Gym</div>
  <h2 style="left:98px">QUICK LINKS</h2>
  <ul>
    <li>Home</li><li>Class descriptions</li><li>Gym description</li><li>Class schedules</li><li>Trainer profiles</li><li>Gym philosophy</li><li>Contact</li>
  </ul>
  <h2 style="left:311px">NEWSLETTER</h2>
  <p class="small abs" style="left:311px;top:88px;width:250px">Subscribe newsletter to receive the latest news and updates direct to your inbox.</p>
  <div class="field"><svg width="13" height="10" viewBox="0 0 20 16"><rect x="1" y="1" width="18" height="14" rx="2" fill="#777"/><path d="M2 3l8 6 8-6" stroke="#fff" stroke-width="2" fill="none"/></svg>ENTER YOUR MAIL ID</div>
  <div class="subscribe">SUBSCRIBE</div>
  <h2 style="left:593px">CONTACT US</h2>
  <div class="info" style="top:92px"><svg width="10" height="14" viewBox="0 0 10 14"><path d="M5 0a5 5 0 0 0-5 5c0 4 5 9 5 9s5-5 5-9a5 5 0 0 0-5-5z" fill="#fff"/><circle cx="5" cy="5" r="2" fill="#0a99c8"/></svg><span style="width:210px">Neque porro quisquam est, qui dolorem ipsum quia dolor sit amet</span></div>
  <div class="info" style="top:150px"><svg width="12" height="12" viewBox="0 0 24 24"><path fill="#fff" d="M6.6 10.8a15 15 0 0 0 6.6 6.6l2.2-2.2c.3-.3.7-.4 1-.2 1.1.4 2.3.6 3.6.6.6 0 1 .4 1 1V20c0 .6-.4 1-1 1A17 17 0 0 1 3 4c0-.6.4-1 1-1h3.5c.6 0 1 .4 1 1 0 1.3.2 2.5.6 3.6.1.3 0 .7-.2 1z"/></svg>1800-555-012</div>
  <div class="info" style="top:175px"><svg width="12" height="10" viewBox="0 0 20 16"><rect x="1" y="1" width="18" height="14" rx="2" fill="none" stroke="#fff" stroke-width="2"/><path d="M2 3l8 6 8-6" stroke="#fff" stroke-width="2" fill="none"/></svg>info@summitgym.ae</div>
</footer>

<div class="bottom-bar">
  <small>&copy;2015 Summit Bodyform Gym. All rights reserved.</small>
  <div class="social"><b></b><b></b><b></b><b></b></div>
</div>

</body>
</html>
```